International Film making Business needs the 5 Logos provided made into a POSTER Format

Design Task:
CREATE A POSTER DESIGN USING THE 5 LOGOS PROVIDED. The BOLD BRIGHT HORIZON LOGO should stand out from the others by being in the middle with the other 4 logos connected to it somehow.

The 5 Businesses already has their 5 Logos, all similar in design to each other.

BOLD BRIGHT HORIZON is the Main Logo that encompasses the other 4 Logos. So it must stand out more and it is like the Overall Business entity that incorporates the other 4 Logos.

What is required is that by using the 5 Logo designs provided, create a cool graphic artwork that somehow incorporates ALL of the 5 Logos - But having the BOLD BRIGHT HORIZON Logo at the forefront/most important/standing out the most.
- BOLD BRIGHT HORIZON will probably be bigger than the others
- and could be changed into 3D.

I have attached all 5 logos and a hand drawn example of how the BOLD BRIGHT HORIZONS could stand out from the rest.

THE DESIGNS OF THE LOGOS SHOULD NOT BE CHANGED (except the BOLDBRIGHTHORIZON which can be 3D)

Please do not be restricted with the sample idea. Creativity is encouraged

DIMENSION: 3000 mm x 6000 mm
high resolution graphic

Logo Text

bold bright , bold bright pictures, bold bright legends, bold bright groovy, BOLD BRIGHT HORIZONS

Requirements
Must have
• USE THE 5 LOGOS PROVIDED ONLY - Only BOLD BRIGHT HORIZON can be changed into 3D only
Nice to have
• Eye catching design, showing the Bold Bright Horizon as the most powerful Logo that has the other 4 as subordinate companies
Should not have
• ANY CHANGE IN THE 5 LOGO DESIGNS (EXcept 3D for Bold Bright Horizons)

```html
<!DOCTYPE html>
<html lang="en">
<head>
<meta charset="utf-8">
<title>Bold Bright Horizons – Poster</title>
<link rel="stylesheet" href="https://fonts.googleapis.com/css2?family=Cinzel:wght@600;700&family=Montserrat:wght@500&display=swap">
<style>
  :root {
    --bg: #000000;
    --frame: #4a3a1a;
    --gold: #c8952a;
    --silver: #c9c9c9;
    --blue: #2f8fd8;
    --spectrum: #e8741c;
    --steel: #8a8a8a;
    --violet: #7a2fc4;
    --white: #ffffff;
  }
  html, body {
    margin: 0;
    padding: 0;
    width: 1200px;
    height: 600px;
    overflow: hidden;
    background: var(--bg);
  }
  .poster { display: block; width: 1200px; height: 600px; }
  .border-frame { fill: none; stroke: var(--frame); stroke-width: 1.5; }
  .brand-name { font-family: "Cinzel", serif; font-weight: 700; letter-spacing: 1px; }
  .brand-dot { stroke: none; }
  .name-blue { fill: var(--blue); }
  .name-spectrum { fill: var(--spectrum); }
  .name-steel { fill: var(--steel); }
  .name-violet { fill: var(--violet); }
  .name-gold { fill: var(--gold); }
  .web-address { font-family: "Montserrat", sans-serif; font-weight: 500; fill: var(--white); font-size: 21px; letter-spacing: 0.5px; }
</style>
</head>
<body>
<svg class="poster" viewBox="0 0 1200 600" xmlns="http://www.w3.org/2000/svg" role="img" aria-label="Bold Bright Horizons poster with four subsidiary brands">
  <defs>
    <linearGradient id="gold-ring" x1="0" y1="0" x2="1" y2="1">
      <stop offset="0" stop-color="#f3d27a"/>
      <stop offset="0.35" stop-color="#b07a1e"/>
      <stop offset="0.6" stop-color="#e6b650"/>
      <stop offset="1" stop-color="#8a5a12"/>
    </linearGradient>
    <linearGradient id="silver-ring" x1="0" y1="0" x2="0" y2="1">
      <stop offset="0" stop-color="#f2f2f2"/>
      <stop offset="0.5" stop-color="#8c8c8c"/>
      <stop offset="1" stop-color="#e0e0e0"/>
    </linearGradient>
    <radialGradient id="spot-glow" cx="0.5" cy="0.4" r="0.55">
      <stop offset="0" stop-color="#ffffff"/>
      <stop offset="0.35" stop-color="#bdbdbd"/>
      <stop offset="1" stop-color="#000000"/>
    </radialGradient>
    <radialGradient id="center-glow" cx="0.38" cy="0.35" r="0.5">
      <stop offset="0" stop-color="#ffffff"/>
      <stop offset="0.3" stop-color="#8a8a8a"/>
      <stop offset="0.75" stop-color="#000000"/>
    </radialGradient>
  </defs>

  <rect class="border-frame" x="84" y="46" width="1037" height="508"/>

  <!-- top subsidiaries -->
  <g class="badge badge-bold-bright">
    <ellipse cx="246" cy="125" rx="218" ry="93" fill="url(#silver-ring)"/>
    <ellipse cx="246" cy="125" rx="211" ry="87" fill="url(#gold-ring)"/>
    <ellipse cx="250" cy="126" rx="182" ry="72" fill="url(#spot-glow)"/>
    <circle class="brand-dot name-blue" cx="172" cy="125" r="24"/>
    <text class="brand-name name-blue" x="206" y="119" font-size="26">BOLD</text>
    <text class="brand-name name-blue" x="206" y="148" font-size="26">BRIGHT</text>
  </g>

  <g class="badge badge-legends">
    <ellipse cx="958" cy="125" rx="218" ry="93" fill="url(#silver-ring)"/>
    <ellipse cx="958" cy="125" rx="211" ry="87" fill="url(#gold-ring)"/>
    <ellipse cx="962" cy="126" rx="182" ry="72" fill="url(#spot-glow)"/>
    <circle class="brand-dot name-spectrum" cx="880" cy="125" r="24"/>
    <text class="brand-name name-spectrum" x="914" y="119" font-size="24">BOLD BRIGHT</text>
    <text class="brand-name name-spectrum" x="914" y="148" font-size="24">LEGENDS</text>
  </g>

  <!-- main brand -->
  <g class="hub badge-horizons">
    <ellipse cx="600" cy="300" rx="428" ry="190" fill="url(#silver-ring)"/>
    <ellipse cx="600" cy="300" rx="418" ry="182" fill="url(#gold-ring)"/>
    <ellipse cx="616" cy="290" rx="360" ry="165" fill="url(#center-glow)"/>
    <circle class="brand-dot name-gold" cx="410" cy="300" r="52"/>
    <text class="brand-name name-gold" x="480" y="285" font-size="44">BOLD BRIGHT</text>
    <text class="brand-name name-gold" x="480" y="333" font-size="44">HORIZONS</text>
    <text class="web-address" x="482" y="363">boldbrighthorizons.com.au</text>
  </g>

  <!-- bottom subsidiaries -->
  <g class="badge badge-pictures">
    <ellipse cx="246" cy="483" rx="218" ry="93" fill="url(#silver-ring)"/>
    <ellipse cx="246" cy="483" rx="211" ry="87" fill="url(#gold-ring)"/>
    <ellipse cx="250" cy="484" rx="182" ry="72" fill="url(#spot-glow)"/>
    <circle class="brand-dot name-steel" cx="168" cy="483" r="24"/>
    <text class="brand-name name-steel" x="202" y="477" font-size="24">BOLD BRIGHT</text>
    <text class="brand-name name-steel" x="202" y="506" font-size="24">PICTURES</text>
  </g>

  <g class="badge badge-groovy">
    <ellipse cx="958" cy="483" rx="218" ry="93" fill="url(#silver-ring)"/>
    <ellipse cx="958" cy="483" rx="211" ry="87" fill="url(#gold-ring)"/>
    <ellipse cx="962" cy="484" rx="182" ry="72" fill="url(#spot-glow)"/>
    <circle class="brand-dot name-violet" cx="880" cy="483" r="24"/>
    <text class="brand-name name-violet" x="914" y="477" font-size="24">BOLD BRIGHT</text>
    <text class="brand-name name-violet" x="914" y="506" font-size="24">GROOVY</text>
  </g>
</svg>
</body>
</html>
```